I need a SEO-friendly Wordpress website (making sure to style H1, H2, H3, etc correctly) for a Hawaii-based law firm called Meridian Crest Legal Group. Comparable websites include https://brvlaw.example/ and https://www.lomrit.example/ for design reference. The current copy on the TarnAdvocate.example website can be used.

```html
<!DOCTYPE html>
<html lang="en">
<head>
<meta charset="utf-8">
<title>Meridian Crest Legal Group</title>
<link rel="stylesheet" href="https://fonts.googleapis.com/css2?family=Playfair+Display:wght@700&family=Raleway:wght@400;500;600&family=Open+Sans:wght@400;600&display=swap">
<style>
:root{
  --brown:#8c3c0f;
  --rust:#a8521a;
  --orange:#c0661e;
  --heading:#a4471a;
  --text:#8a8a8a;
  --dark:#3a3a3a;
  --grey-bg:#f3f3f3;
  --white:#ffffff;
}
*{box-sizing:border-box;margin:0;padding:0}
html,body{width:706px;height:1200px;overflow:hidden;background:var(--white)}
body{font-family:"Open Sans",Arial,sans-serif;color:var(--text)}
.hero{position:relative;height:384px;overflow:hidden}
.hero-photo{position:absolute;inset:0;background:linear-gradient(180deg,#c46a26 0%,#b45a1a 40%,#a04a14 75%,#8a3d10 100%)}
.hero-photo::after{content:"";position:absolute;inset:0;background:radial-gradient(ellipse at 50% 30%,rgba(255,200,130,.35),rgba(0,0,0,0) 60%)}
.hero-mark{position:absolute;left:298px;top:44px;width:110px;height:110px;border-radius:50%;background:rgba(240,140,50,.55)}
.hero-title{position:absolute;top:86px;width:100%;text-align:center;font-family:"Playfair Display",Georgia,serif;font-size:32px;color:var(--white)}
.hero-tagline{position:absolute;top:218px;width:100%;text-align:center;font-family:"Raleway",Arial,sans-serif;font-weight:500;font-size:28px;line-height:36px;color:var(--white)}
.arrow{position:absolute;top:160px;width:34px;height:34px;border-radius:50%;background:rgba(255,255,255,.35);display:flex;align-items:center;justify-content:center}
.arrow.prev{left:24px}.arrow.next{right:24px}
h2{font-family:"Raleway",Arial,sans-serif;font-weight:500;color:var(--heading);text-align:center}
.btn{display:inline-block;background:var(--rust);color:var(--white);font-family:"Raleway",Arial,sans-serif;font-size:11px;font-weight:600;letter-spacing:.5px;padding:9px 14px;text-decoration:none}
.about{height:216px;text-align:center;padding-top:36px}
.about h2{font-size:28px;letter-spacing:1px}
.about h3{font-family:"Raleway",Arial,sans-serif;font-weight:600;font-size:14px;color:var(--orange);margin-top:10px}
.about p{font-size:10px;line-height:15px;width:390px;margin:8px auto 18px}
.practice{height:325px;background:var(--grey-bg);padding-top:42px}
.practice h2{font-size:28px}
.cards{display:flex;justify-content:center;gap:30px;margin-top:28px}
.card{width:140px;height:180px;text-align:center;padding-top:16px}
.card.featured{background:var(--white);box-shadow:0 2px 10px rgba(0,0,0,.12);border-radius:4px}
.card-icon{width:56px;height:56px;border-radius:50%;background:#f2dcc6;margin:0 auto;display:flex;align-items:center;justify-content:center}
.card h3{font-family:"Raleway",Arial,sans-serif;font-weight:600;font-size:13px;color:var(--dark);margin-top:14px}
.card p{font-size:8.5px;line-height:13px;margin:6px 8px 10px}
.card a{font-size:9px;color:var(--orange);text-decoration:underline;font-weight:600}
.experience{height:210px;text-align:center;padding-top:40px}
.experience h2{font-size:30px;line-height:36px;color:var(--heading)}
.experience p{font-size:9.5px;line-height:14px;width:380px;margin:16px auto 16px}
.footer{height:65px;background:var(--brown);color:var(--white);position:relative;padding:14px 0 0 34px}
.footer nav{display:flex;gap:12px;font-family:"Raleway",Arial,sans-serif;font-size:11px}
.footer nav span.sep{opacity:.7}
.footer small{display:block;font-size:8px;margin-top:10px;opacity:.9}
.social{position:absolute;right:30px;top:22px;display:flex;gap:8px}
.social span{width:20px;height:20px;border-radius:50%;background:var(--white)}
</style>
</head>
<body>
<header class="hero">
  <div class="hero-photo" role="img" aria-label="City skyline photograph in warm orange tones"></div>
  <div class="hero-mark"></div>
  <h1 class="hero-title">Meridian Crest Legal Group</h1>
  <p class="hero-tagline">Dedicated to making sure you<br>receive the care and attention<br>you need</p>
  <span class="arrow prev"><svg width="12" height="12" viewBox="0 0 12 12"><path d="M8 1 3 6l5 5" fill="none" stroke="#fff" stroke-width="2"/></svg></span>
  <span class="arrow next"><svg width="12" height="12" viewBox="0 0 12 12"><path d="M4 1l5 5-5 5" fill="none" stroke="#fff" stroke-width="2"/></svg></span>
</header>

<section class="about">
  <h2>ABOUT US</h2>
  <h3>Lawyers Serving the Big Island and Neighboring Islands</h3>
  <p>Our experienced attorneys at Meridian Crest Legal Group serve clients across Hawaii with a wide range of litigation expertise, including family matters, personal injury, business law, real estate and trusts.</p>
  <a class="btn" href="#">READ MORE</a>
</section>

<section class="practice">
  <h2>PRACTICE AREAS</h2>
  <div class="cards">
    <article class="card">
      <div class="card-icon" role="img" aria-label="Family and divorce icon"></div>
      <h3>Family &amp; Divorce</h3>
      <p>Our lawyers handle all aspects of family law on the Big Island and neighboring islands.</p>
      <a href="#">READ MORE</a>
    </article>
    <article class="card featured">
      <div class="card-icon" role="img" aria-label="Personal injury icon"></div>
      <h3>Personal Injury</h3>
      <p>Dealing with injury and wrongful death claims is hard enough on its own for the family.</p>
      <a href="#">READ MORE</a>
    </article>
    <article class="card">
      <div class="card-icon" role="img" aria-label="Corporate and intellectual property icon"></div>
      <h3>Corporate &amp; IP</h3>
      <p>The attorneys at our firm have been helping Big Island businesses with all their legal needs.</p>
      <a href="#">READ MORE</a>
    </article>
    <article class="card">
      <div class="card-icon" role="img" aria-label="Real estate icon"></div>
      <h3>Real Estate</h3>
      <p>Our lawyers assist with home owners, buyers and property developers on island.</p>
      <a href="#">READ MORE</a>
    </article>
  </div>
</section>

<section class="experience">
  <h2>Over 70 years of combined practice,<br>specializing in</h2>
  <p>Our team serves as the West Hawaii headquarters for litigation with representation on behalf of individuals and corporations involved in a wide range of legal matters.</p>
  <a class="btn" href="#">FREE CONSULTANT</a>
</section>

<footer class="footer">
  <nav><span>Home</span><span class="sep">|</span><span>Practice Areas</span><span class="sep">|</span><span>Attorneys</span><span class="sep">|</span><span>Blog</span><span class="sep">|</span><span>Contact Us</span></nav>
  <small>Copyright © Meridian Crest Legal Group. All Rights Reserved.</small>
  <div class="social"><span></span><span></span><span></span><span></span></div>
</footer>
</body>
</html>
```